Design Startseite Kanzlei-Homepage
Zielgruppe
Wir sind eine Rechtsanwaltskanzlei in Kempten (Allgäu) und regional sowie überregional in verschiedenen Rechtsgebieten tätig. Unsere Zielgruppe sind sowohl private als auch gewerbliche Mandanten.
Aufgabenstellung
Die bestehende Gestaltung wirkt derzeit aus unserer Sicht überholt. Insbesondere soll das bislang dominierende Rot vollständig entfallen.
Stattdessen stellen wir uns ein modernes, hochwertiges Erscheinungsbild vor, primär in dunklen Farbtönen (Anthrazit/Schwarz) kombiniert mit Beige- bzw. warmen Naturtönen. Ziel ist eine klare visuelle Anlehnung an unsere Kanzleiräumlichkeiten (siehe Fotos).
Die Webseite soll insgesamt moderner, klarer und visuell anspruchsvoller wirken, ohne an Seriosität und Zugänglichkeit einzubüßen. Die Balance zwischen hochwertigem Erscheinungsbild und mandantenorientierter Nutzerführung steht für uns im Vordergrund.

```html
<!DOCTYPE html>
<html lang="de">
<head>
<meta charset="utf-8">
<title>Kanzlei am Lindenhof – Kontakt</title>
<link href="https://fonts.googleapis.com/css2?family=Cinzel:wght@400;500;600&family=Fira+Sans+Condensed:wght@400;500;600&display=swap" rel="stylesheet">
<style>
:root{
  --brown:#8b7356;
  --field:#f0f0f0;
  --text:#3a3a3a;
  --footer:#3c3c3c;
  --footer-text:#f2f2f2;
  --line:#8a8a8a;
}
*{box-sizing:border-box;margin:0;padding:0}
html,body{width:1200px;height:700px;overflow:hidden;background:#fff}
body{position:relative;font-family:"Fira Sans Condensed",sans-serif;color:var(--text)}
.map{position:absolute;left:0;top:19px;width:550px;height:410px;background:linear-gradient(135deg,#ececec,#dcdcdc)}
.edit-tile{position:absolute;left:550px;top:19px;width:56px;height:56px;background:var(--brown);display:flex;align-items:center;justify-content:center}
.eyebrow{position:absolute;left:640px;top:36px;font-family:"Cinzel",serif;font-size:10px;color:var(--brown);letter-spacing:.3px}
.title{position:absolute;left:640px;top:58px;font-family:"Cinzel",serif;font-weight:600;font-size:18px;color:var(--brown);letter-spacing:.4px}
.field{position:absolute;background:var(--field);font-size:9.5px;color:#444;padding-left:10px;display:flex;align-items:center}
.field.area{align-items:flex-start;padding-top:12px}
.chev{position:absolute;right:10px;top:12px}
.grip{position:absolute;right:3px;bottom:3px}
.send{position:absolute;left:640px;top:376px;width:107px;height:24px;background:var(--brown);color:#fff;font-weight:600;font-size:11px;display:flex;align-items:center;justify-content:center;letter-spacing:.3px}
.footer{position:absolute;left:0;top:448px;width:1200px;height:252px;background:var(--footer);color:var(--footer-text)}
.brand{position:absolute;left:319px;top:61px;font-weight:600;font-size:11.5px;letter-spacing:.4px;color:#fff;white-space:nowrap}
.contact{position:absolute;left:319px;top:104px;font-size:7px;line-height:1.4;list-style:none}
.contact li{display:flex;gap:5px;margin-bottom:6px}
.contact .ico{color:var(--brown);width:7px}
.follow{position:absolute;left:319px;top:168px;font-size:7px}
.social{position:absolute;left:319px;top:181px;display:flex;gap:7px}
.social span{width:16px;height:16px;background:var(--brown)}
.col-title{position:absolute;top:64px;font-family:"Cinzel",serif;font-size:8.5px;color:#fff;letter-spacing:.3px}
.menu{position:absolute;top:104px;list-style:none;font-size:7px}
.menu li{border-bottom:1px solid var(--line);padding-bottom:3px;margin-bottom:5px;width:max-content;min-width:44px}
.call{position:absolute;left:758px;top:97px;width:116px;height:25px;border:1px solid #6a6a6a;display:flex;align-items:center}
.call i{width:26px;height:23px;background:var(--brown);display:flex;align-items:center;justify-content:center}
.call span{font-size:9px;padding-left:6px;color:#fff}
.copy{position:absolute;left:758px;top:189px;font-family:"Cinzel",serif;font-size:6px;color:#ddd}
</style>
</head>
<body>
<div class="map" role="img" aria-label="Stadtplan mit Standort der Kanzlei"></div>
<div class="edit-tile">
  <svg width="22" height="22" viewBox="0 0 22 22" fill="none" stroke="#fff" stroke-width="1.4"><path d="M15 3H3v16h16V8"/><path d="M9 13l1-3 8-8 2 2-8 8z"/></svg>
</div>
<div class="eyebrow">KONTAKT</div>
<h1 class="title">ONLINE-FORMULAR</h1>

<div class="field" style="left:637px;top:132px;width:200px;height:36px">Name*</div>
<div class="field" style="left:843px;top:132px;width:200px;height:36px">E-Mail</div>
<div class="field" style="left:637px;top:185px;width:406px;height:36px">Telefon</div>
<div class="field" style="left:637px;top:238px;width:406px;height:31px">Betreff
  <svg class="chev" width="9" height="6" viewBox="0 0 9 6"><path d="M1 1l3.5 3.5L8 1" stroke="#999" fill="none" stroke-width="1.3"/></svg>
</div>
<div class="field area" style="left:637px;top:286px;width:406px;height:57px">Nachricht schreiben
  <svg class="grip" width="8" height="8" viewBox="0 0 8 8"><path d="M1 8L8 1M4 8L8 4M7 8L8 7" stroke="#777"/></svg>
</div>
<div class="send">Absenden &gt;&gt;</div>

<footer class="footer">
  <div class="brand">KANZLEI AM LINDENHOF</div>
  <ul class="contact">
    <li><span class="ico">⌂</span><span>Kanzlei am Lindenhof<br>Ahornweg 14, 87400 Talbach</span></li>
    <li><span class="ico">☏</span><span>0831 555 204 17</span></li>
    <li><span class="ico">✉</span><span>info@kanzlei-lindenhof.de</span></li>
  </ul>
  <div class="follow">Folge uns:</div>
  <div class="social"><span></span><span></span><span></span></div>

  <div class="col-title" style="left:465px">RECHTSGEBIETE</div>
  <ul class="menu" style="left:466px">
    <li>Familienrecht</li><li>Arbeitsrecht</li><li>Verkehrsrecht</li><li>Strafrecht</li><li>Erbrecht</li><li>Mietrecht / Wohnungseigentumsrecht</li>
  </ul>
  <div class="col-title" style="left:632px">LINKS</div>
  <ul class="menu" style="left:633px">
    <li>Startseite</li><li>Rechtsgebiete</li><li>Kanzlei</li><li>Kontakt</li>
  </ul>
  <div class="col-title" style="left:758px;top:62px">BERATUNG</div>
  <div class="call"><i><svg width="10" height="10" viewBox="0 0 10 10"><path d="M2 1l2 2-1 1.2c.6 1.3 1.5 2.2 2.8 2.8L7 6l2 2-1.2 1.5C4.5 9 1 5.5.5 2.2z" fill="#fff"/></svg></i><span>+49 831 555 204 17</span></div>
  <div class="copy">COPYRIGHT © FELDMANN MEDIENDESIGN 2026</div>
</footer>
</body>
</html>
```